Enhance Landing Page

Actual: https://thecoralparlor.com/aplique-no-litoral-lp-port/

I need a better design for this page:
Using this shortcodes : https://bolder.qrxlayouts.net
Rules:
. Keep the page header
. Keep the footer

```html
<!DOCTYPE html>
<html lang="pt">
<head>
<meta charset="utf-8">
<title>The Coral Parlor – Invista na Florida</title>
<link rel="stylesheet" href="https://fonts.googleapis.com/css2?family=Lato:wght@400;700;900&family=Open+Sans:wght@400;600;700&display=swap">
<style>
:root{
  --teal:#1a9bb7;
  --teal-dark:#15859e;
  --green:#2bb02b;
  --orange:#f26a21;
  --crimson:#d3154f;
  --ink:#222;
  --body:#555;
  --light:#f2f2f2;
  --white:#fff;
  --bar:#1d1d1d;
}
*{box-sizing:border-box;margin:0;padding:0}
html,body{width:1200px;height:4412px;overflow:hidden}
body{font-family:"Open Sans",Arial,sans-serif;color:var(--body);background:var(--white);position:relative}
section,header,footer{position:absolute;left:0;width:1200px}
.abs{position:absolute}
h2,h3,.heading{font-family:"Lato",Arial,sans-serif;font-weight:900;text-transform:uppercase}
.accent-line{position:absolute;height:3px;width:70px;background:var(--teal)}
.btn{position:absolute;display:flex;align-items:center;justify-content:center;font-family:"Lato",Arial,sans-serif;font-weight:900;text-transform:uppercase;color:var(--white);letter-spacing:.5px}
.brand{font-family:"Lato",Arial,sans-serif;font-weight:900;color:var(--crimson);text-transform:uppercase;letter-spacing:2px;white-space:nowrap}

/* header */
.site-header{top:0;height:106px;background:var(--white);z-index:3}
.site-header .tab{position:absolute;left:520px;top:60px;width:160px;height:80px;border-radius:0 0 80px 80px;background:var(--white)}
.phone-badge{position:absolute;background:var(--green);color:var(--white);font:700 11px "Open Sans",sans-serif;display:flex;align-items:center;gap:6px;padding:0 10px;border-radius:3px}
.phone-line{position:absolute;font:600 11px "Open Sans",sans-serif;color:var(--ink);display:flex;gap:14px;white-space:nowrap}
.phone-line span{display:flex;align-items:center;gap:5px}
.flag{display:inline-block;width:12px;height:9px}
.cta-link{position:absolute;display:flex;align-items:center;gap:8px;font:900 11px "Lato",sans-serif;color:var(--ink);text-transform:uppercase;line-height:1.2}
.cta-link .dot{width:34px;height:34px;border-radius:50%;display:flex;align-items:center;justify-content:center}

/* hero */
.hero{top:106px;height:506px}
.hero .photo{position:absolute;inset:0;background:linear-gradient(180deg,#7b5a4a 0%,#b8845e 35%,#5e4637 62%,#2b2520 100%)}
.hero .shade{position:absolute;inset:0;background:linear-gradient(90deg,rgba(0,0,0,.45),rgba(0,0,0,0) 60%)}
.hero h1{position:absolute;left:147px;top:316px;font:900 32px/1.1 "Lato",sans-serif;color:var(--white);text-transform:uppercase;letter-spacing:1px}
.hero .lead{position:absolute;left:147px;top:410px;font:700 15px/1.35 "Open Sans",sans-serif;color:var(--white);text-transform:uppercase;letter-spacing:2px}
.hero-form{position:absolute;left:735px;top:47px;width:323px;height:459px;background:rgba(26,155,183,.88)}
.hero-form h3{position:absolute;left:30px;top:22px;font-size:22px;color:var(--white);letter-spacing:1px}
.hero-form .field{position:absolute;left:30px;width:264px;height:40px;border:2px solid rgba(255,255,255,.85);font:700 10px "Open Sans",sans-serif;color:var(--white);padding:8px 12px;text-transform:uppercase}
.hero-form .btn{left:30px;top:394px;width:264px;height:47px;background:var(--orange);font-size:18px}

/* about */
.about{top:612px;height:573px;background:var(--white)}
.about .photo{position:absolute;left:144px;top:55px;width:456px;height:459px;background:linear-gradient(135deg,#8a8f8e,#d9d5cc 45%,#6d6a63);box-shadow:0 2px 10px rgba(0,0,0,.25)}
.about h2{position:absolute;left:659px;top:125px;width:420px;font-size:26px;line-height:1.3;color:var(--ink)}
.about p{position:absolute;left:659px;width:400px;font-size:14px;line-height:1.5}

/* services */
.services{top:1185px;height:470px;background:var(--teal)}
.section-title{position:absolute;left:0;width:1200px;text-align:center;font-size:26px}
.service-card{position:absolute;top:188px;width:218px;height:206px;background:rgba(255,255,255,.1);border:1px solid rgba(255,255,255,.35);color:var(--white);text-align:center}
.service-card.active{background:var(--green);border:3px solid var(--white)}
.service-card svg{position:absolute;left:84px;top:52px}
.service-card .label{position:absolute;left:0;width:100%;top:135px;font:700 14px "Open Sans",sans-serif;text-transform:uppercase}
.service-card.active svg{top:22px}
.service-card.active .label{top:95px}
.service-card .desc{position:absolute;left:20px;right:20px;top:118px;font-size:11px;line-height:1.35}

/* vision */
.vision{top:1655px;height:382px}
.vision .photo{position:absolute;inset:0;background:linear-gradient(180deg,#2d3540 0%,#59606b 40%,#323845 75%,#1c2028 100%)}
.vision h2{position:absolute;top:98px;left:0;width:1200px;text-align:center;font-size:40px;color:var(--white)}
.vision p{position:absolute;top:163px;left:0;width:1200px;text-align:center;font:700 19px/1.4 "Open Sans",sans-serif;color:var(--white)}
.vision .btn{left:482px;top:244px;width:194px;height:47px;background:var(--crimson);font-size:14px}

/* specialist */
.specialist{top:2037px;height:933px;background:var(--light)}
.gallery-item{position:absolute;width:297px;height:247px}
.specialist .btn.schedule{left:467px;top:162px;width:242px;height:53px;background:var(--orange);font-size:15px}
.specialist .btn.more{left:520px;top:829px;width:177px;height:45px;background:var(--crimson);font-size:14px;gap:10px}

/* builder */
.builder{top:2970px;height:352px;background:var(--crimson)}
.builder h2{position:absolute;top:38px;left:0;width:1200px;text-align:center;font-size:30px;color:var(--white)}
.builder p{position:absolute;top:100px;left:230px;width:740px;text-align:center;color:var(--white);font-size:13px;line-height:1.4}
.stat{position:absolute;top:173px;width:218px;height:129px;border:3px solid var(--white);color:var(--white);display:flex;flex-direction:column;align-items:center;justify-content:center;text-align:center;font-family:"Open Sans",sans-serif}
.stat b{font-weight:400;font-size:30px;line-height:1.1}
.stat span{font-weight:600;font-size:17px;line-height:1.25}
.stat.small b{font-size:22px}

/* contact */
.contact{top:3322px;height:706px;background:var(--white)}
.contact h2{position:absolute;top:58px;left:0;width:1200px;text-align:center;font-size:30px;color:var(--orange)}
.contact .intro{position:absolute;top:114px;left:320px;width:560px;text-align:center;font-size:13px;line-height:1.45;color:var(--ink)}
.contact .photo{position:absolute;left:550px;top:212px;width:511px;height:417px;background:linear-gradient(180deg,#f4c36a 0%,#e59a3c 40%,#8c6a3a 75%,#4f5a2e 100%)}
.touch-card{position:absolute;left:135px;top:241px;width:471px;height:359px;background:var(--white);box-shadow:0 3px 14px rgba(0,0,0,.22)}
.touch-card h3{position:absolute;left:41px;top:30px;font-size:22px;color:var(--crimson)}
.touch-card .field{position:absolute;border:1px solid #cfcfcf;font-size:10px;color:#777;padding:10px 10px;background:#fafafa}
.touch-card .btn{left:41px;top:280px;width:395px;height:47px;background:var(--orange);font-size:18px}

/* footer */
.site-footer{top:4028px;height:317px;background:linear-gradient(180deg,#fafafa 0%,#ececec 100%)}
.site-footer .skyline{position:absolute;left:0;top:0;width:1200px;height:110px;background:linear-gradient(180deg,rgba(200,200,200,0) 0%,rgba(190,190,190,.45) 100%)}
.office{position:absolute;left:85px;font-size:11px;line-height:1.45;color:var(--ink)}
.office b{font:900 13px "Lato",sans-serif;color:var(--crimson);display:flex;align-items:center;gap:6px}
.bottom-bar{position:absolute;left:0;top:4345px;width:1200px;height:67px;background:var(--bar);color:#ccc;font:700 10px "Open Sans",sans-serif;text-transform:uppercase}
.bottom-bar .copy{position:absolute;left:85px;top:27px}
.bottom-bar nav{position:absolute;right:90px;top:27px;display:flex;gap:36px}
</style>
</head>
<body>

<header class="site-header">
  <div class="tab"></div>
  <div class="phone-badge" style="left:229px;top:35px;height:21px">
    <svg width="11" height="11" viewBox="0 0 24 24"><path fill="#fff" d="M6.6 10.8a15.1 15.1 0 0 0 6.6 6.6l2.2-2.2a1 1 0 0 1 1-.25 11.4 11.4 0 0 0 3.6.57 1 1 0 0 1 1 1V20a1 1 0 0 1-1 1A17 17 0 0 1 3 4a1 1 0 0 1 1-1h3.5a1 1 0 0 1 1 1c0 1.25.2 2.45.57 3.57a1 1 0 0 1-.25 1z"/></svg>
    USA +17865550142
  </div>
  <div class="phone-line" style="left:196px;top:63px">
    <span><i class="flag" style="background:var(--green)"></i>+55 21 3000-0147</span>
    <span><i class="flag" style="background:#3a4f9c"></i>+1 (855) 555-0193</span>
  </div>
  <div class="brand abs" style="left:475px;top:36px;width:250px;text-align:center;font-size:24px">Coral Parlor</div>
  <div class="cta-link" style="left:773px;top:38px">
    <span class="dot" style="background:var(--crimson)"><svg width="16" height="16" viewBox="0 0 24 24"><path fill="#fff" d="M4 4h16v11H8l-4 4z"/></svg></span>
    <span>Fale com um<br>agente</span>
  </div>
  <div class="cta-link" style="left:917px;top:38px">
    <span class="dot" style="background:var(--teal)"><svg width="16" height="16" viewBox="0 0 24 24"><rect x="4" y="6" width="16" height="14" fill="none" stroke="#fff" stroke-width="2"/><path d="M4 10h16M8 3v5M16 3v5" stroke="#fff" stroke-width="2"/></svg></span>
    <span>Agende uma<br>conversa</span>
  </div>
</header>

<section class="hero">
  <div class="photo" role="img" aria-label="Luxury Florida villa with a tiled roof and palm trees at sunset"></div>
  <div class="shade"></div>
  <h1>Invista na Florida<br>e rentabilize tranquilidade</h1>
  <p class="lead">Conheça as melhores oportunidades de<br>investimentos na Florida</p>
  <form class="hero-form">
    <h3>Contact us</h3>
    <div class="field" style="top:76px">Name</div>
    <div class="field" style="top:125px">E-mail</div>
    <div class="field" style="top:175px">Phone</div>
    <div class="field" style="top:229px;height:100px">Message</div>
    <div class="btn">Submit</div>
  </form>
</section>

<section class="about">
  <div class="photo" role="img" aria-label="Lounge interior with armchairs, plants and large display panels"></div>
  <div class="accent-line" style="left:659px;top:111px"></div>
  <h2>Presentes no Brasil e<br>Estados Unidos</h2>
  <p style="top:235px">O The Coral Parlor possui um Lounge permanente no Rio de Janeiro, Brasil e em Orlando, na Florida. Com um conceito inovador de atendimento 360º, assessorando os clientes que desejam comprar um imóvel nos Estados Unidos, seja para investir ou Morar.</p>
  <p style="top:367px">Com a parceria exclusiva da Harbison, a maior construtora dos Estados Unidos, garantimos as melhores escolhas para você e sua família! Nossos especialistas possuem visão 360º para apoia-lo em todo o processo e viver a melhor experiência na compra de um imóvel na América.</p>
</section>

<section class="services">
  <div class="accent-line" style="left:565px;top:73px;background:var(--white)"></div>
  <h2 class="section-title" style="top:94px;color:var(--white)">Our services</h2>

  <div class="service-card" style="left:135px">
    <svg width="50" height="56" viewBox="0 0 50 56"><rect x="6" y="2" width="38" height="52" rx="3" fill="#fff"/><rect x="11" y="7" width="28" height="10" fill="var(--teal)"/><g fill="var(--teal)"><rect x="11" y="22" width="7" height="7"/><rect x="21.5" y="22" width="7" height="7"/><rect x="32" y="22" width="7" height="7"/><rect x="11" y="32" width="7" height="7"/><rect x="21.5" y="32" width="7" height="7"/><rect x="32" y="32" width="7" height="17"/><rect x="11" y="42" width="7" height="7"/><rect x="21.5" y="42" width="7" height="7"/></g></svg>
    <div class="label">Accounting</div>
  </div>

  <div class="service-card active" style="left:368px">
    <svg width="50" height="56" viewBox="0 0 50 56"><rect x="3" y="10" width="44" height="12" fill="#fff"/><rect x="6" y="24" width="38" height="26" fill="#fff"/><rect x="19" y="28" width="12" height="5" fill="var(--green)"/></svg>
    <div class="label">Documentation</div>
    <div class="desc">Sed ut perspiciatis unde omnis iste natus error sit voluptatem accusantium doloremque.</div>
  </div>

  <div class="service-card" style="left:600px">
    <svg width="50" height="56" viewBox="0 0 50 56"><path d="M8 2h34v52l-5-4-5 4-5-4-5 4-5-4-5 4z" fill="#fff"/><g stroke="var(--teal)" stroke-width="3"><path d="M14 12h12M14 20h22M14 28h22M14 36h22"/></g></svg>
    <div class="label">Financial remittances</div>
  </div>

  <div class="service-card" style="left:832px">
    <svg width="50" height="56" viewBox="0 0 50 56"><circle cx="30" cy="16" r="12" fill="#fff"/><path d="M30 9v14M26 12h6a3 3 0 0 1 0 6h-4a3 3 0 0 0 0 6h6" stroke="var(--teal)" stroke-width="2" fill="none"/><path d="M2 38h10l12 4h12a3 3 0 0 1 0 6H20M12 36v18H2z" fill="#fff"/></svg>
    <div class="label">Financing</div>
  </div>
</section>

<section class="vision">
  <div class="photo" role="img" aria-label="Aerial view of a city skyline with tall towers by the water"></div>
  <h2>360 Vision</h2>
  <p>We take care of absolutely everything to<br>make you feel at home in Florida!</p>
  <div class="btn">Click here</div>
</section>

<section class="specialist">
  <div class="accent-line" style="left:565px;top:74px"></div>
  <h2 class="section-title" style="top:96px;color:var(--ink)">Deseja falar com um especialista?</h2>
  <div class="btn schedule">
    <svg width="16" height="16" viewBox="0 0 24 24" style="margin-right:8px"><rect x="3" y="5" width="18" height="16" fill="none" stroke="#fff" stroke-width="2"/><path d="M3 10h18M8 2v5M16 2v5" stroke="#fff" stroke-width="2"/></svg>
    Agendar atendimento
  </div>

  <div class="gallery-item" style="left:144px;top:280px;background:linear-gradient(180deg,#3a3028,#7a5c40 50%,#2a211b)" role="img" aria-label="Clubhouse bar with warm lighting"></div>
  <div class="gallery-item" style="left:453px;top:280px;background:linear-gradient(180deg,#c8794e,#e8a66d 35%,#5a4236 70%,#3c4a2e)" role="img" aria-label="Community clubhouse at sunset"></div>
  <div class="gallery-item" style="left:759px;top:280px;background:linear-gradient(180deg,#3b7fc9,#86b7e6 45%,#4d7a3a 80%,#3a5a2a)" role="img" aria-label="Community entrance gate with palm trees"></div>
  <div class="gallery-item" style="left:144px;top:538px;background:linear-gradient(180deg,#1c1a22,#6b5036 55%,#2f2a24)" role="img" aria-label="Lit stone fountain at dusk"></div>
  <div class="gallery-item" style="left:453px;top:538px;background:linear-gradient(180deg,#24325c,#4a5d92 40%,#8a6a4a 70%,#2a2a34)" role="img" aria-label="Clubhouse building at twilight"></div>
  <div class="gallery-item" style="left:759px;top:538px;background:linear-gradient(180deg,#4f8ec4,#6aa25a 40%,#2fa3c4 75%,#2d6a7a)" role="img" aria-label="Resort pool with palms and a bridge"></div>

  <div class="btn more">Show more
    <svg width="12" height="8" viewBox="0 0 12 8"><path d="M1 1l5 5 5-5" stroke="#fff" stroke-width="2" fill="none"/></svg>
  </div>
</section>

<section class="builder">
  <h2>Harbison</h2>
  <p>HARBISON is more than just a real estate developer. It is one of the largest builders in the US. The commitment to quality, value and integrity is the fundamental basis HARBISON. The condominiums built by HARBISON cater to all lifestyles.</p>
  <div class="stat" style="left:144px"><b>40+</b><span>Cities</span></div>
  <div class="stat" style="left:376px"><b>18</b><span>States</span></div>
  <div class="stat" style="left:606px"><b>1954</b><span>Founded</span></div>
  <div class="stat small" style="left:835px"><b>MORE THAN 600</b><span>Condominiums Under<br>Construction</span></div>
</section>

<section class="contact">
  <h2>Contact us</h2>
  <p class="intro">At vero eos et accusamus et iusto odio dignissimos ducimus qui blanditiis praesentium voluptatum deleniti atque corrupti quo dolores et</p>
  <div class="photo" role="img" aria-label="Family flying a kite in a field at sunset"></div>
  <form class="touch-card">
    <h3>Get in touch</h3>
    <div class="field" style="left:41px;top:74px;width:190px;height:38px">Name</div>
    <div class="field" style="left:244px;top:74px;width:192px;height:38px">Email</div>
    <div class="field" style="left:41px;top:124px;width:190px;height:38px">Phone Number</div>
    <div class="field" style="left:244px;top:124px;width:192px;height:38px">Subject</div>
    <div class="field" style="left:41px;top:177px;width:395px;height:88px">Message</div>
    <div class="btn">Submit</div>
  </form>
</section>

<footer class="site-footer">
  <div class="skyline" role="img" aria-label="Faint city skyline with a ferris wheel"></div>
  <div class="office" style="top:115px">
    <b><svg width="11" height="14" viewBox="0 0 24 30"><path d="M12 0a11 11 0 0 0-11 11c0 8 11 19 11 19s11-11 11-19A11 11 0 0 0 12 0zm0 15a4 4 0 1 1 0-8 4 4 0 0 1 0 8z" fill="var(--crimson)"/></svg>Centro Mar Azul</b>
    2º floor next to the Food Court Av. Atlântica<br>4120, Recreio – RJ – Brazil
  </div>
  <div class="office" style="top:195px">
    <b><svg width="11" height="14" viewBox="0 0 24 30"><path d="M12 0a11 11 0 0 0-11 11c0 8 11 19 11 19s11-11 11-19A11 11 0 0 0 12 0zm0 15a4 4 0 1 1 0-8 4 4 0 0 1 0 8z" fill="var(--crimson)"/></svg>Orlando</b>
    4410 Palm Crest Boulevard, Suite 108, Orlando, USA
  </div>
  <div class="office" style="top:260px;display:flex;align-items:center;gap:6px;color:var(--crimson)">
    <svg width="13" height="10" viewBox="0 0 26 20"><rect width="26" height="20" fill="var(--crimson)"/><path d="M1 1l12 10L25 1" stroke="#fff" stroke-width="2" fill="none"/></svg>
    contact@thecoralparlor.com
  </div>

  <div class="brand abs" style="left:455px;top:145px;width:290px;text-align:center;font-size:30px">Coral Parlor</div>

  <div class="phone-badge" style="left:844px;top:114px;height:30px;font-size:15px;padding:0 14px">
    <svg width="14" height="14" viewBox="0 0 24 24"><path fill="#fff" d="M6.6 10.8a15.1 15.1 0 0 0 6.6 6.6l2.2-2.2a1 1 0 0 1 1-.25 11.4 11.4 0 0 0 3.6.57 1 1 0 0 1 1 1V20a1 1 0 0 1-1 1A17 17 0 0 1 3 4a1 1 0 0 1 1-1h3.5a1 1 0 0 1 1 1c0 1.25.2 2.45.57 3.57a1 1 0 0 1-.25 1z"/></svg>
    USA +17865550142
  </div>
  <div class="phone-line" style="left:806px;top:156px">
    <span><i class="flag" style="background:var(--green)"></i>+55 21 3000-0147</span>
    <span><i class="flag" style="background:#3a4f9c"></i>+1 (855) 555-0193</span>
  </div>
  <div class="cta-link" style="left:786px;top:202px;font-size:13px">
    <span class="dot" style="background:var(--crimson)"><svg width="16" height="16" viewBox="0 0 24 24"><path fill="#fff" d="M4 4h16v11H8l-4 4z"/></svg></span>
    <span>Talk to an<br>agent</span>
  </div>
  <div class="cta-link" style="left:947px;top:202px;font-size:13px">
    <span class="dot" style="background:var(--teal)"><svg width="16" height="16" viewBox="0 0 24 24"><rect x="4" y="6" width="16" height="14" fill="none" stroke="#fff" stroke-width="2"/><path d="M4 10h16M8 3v5M16 3v5" stroke="#fff" stroke-width="2"/></svg></span>
    <span>Schedule a<br>conversation</span>
  </div>
</footer>

<div class="bottom-bar">
  <div class="copy">© 2017 - The Coral Parlor</div>
  <nav><span>Home</span><span>Properties</span><span>Magazine</span><span>Contact</span><span>Terms of use</span></nav>
</div>

</body>
</html>
```